We are a recruitment company based in Norwich/Cambridge England.
I have included our company logo which we want to remain the same.

What we are looking for is a new creative Business card which will really stand out!!

Contact Information for Business Card

Harriet Dunmore
email: Harriet@plavex.co.uk
Address: Brackwell House
Fenmoor Enterprise Park
Partridge Way
Norwich
QB9 3KX
Tel:01632 960418

```html
<!DOCTYPE html>
<html lang="en">
<head>
<meta charset="utf-8">
<title>Plavex Business Card</title>
<link href="https://fonts.googleapis.com/css2?family=Roboto:wght@400;500;700&display=swap" rel="stylesheet">
<style>
  :root {
    --bg: #262626;
    --card-white: #f3f3f3;
    --brand-green: #8cc43f;
    --brand-grey: #8a8a8c;
    --text-dark: #4a4a4a;
    --text-mid: #6f6f6f;
    --divider: #c9c9c9;
    --white: #ffffff;
  }
  * { margin: 0; padding: 0; box-sizing: border-box; }
  html, body {
    width: 1200px; height: 960px; overflow: hidden;
    background: var(--bg);
    font-family: "Roboto", Arial, sans-serif;
  }
  .canvas { position: relative; width: 1200px; height: 960px; }

  .card {
    position: absolute; left: 320px; width: 600px; height: 340px;
    box-shadow: 0 4px 14px rgba(0,0,0,.45);
  }
  .card--front { top: 95px; background: var(--card-white); }
  .card--back { top: 493px; background: var(--brand-green); }

  .brand {
    position: absolute; display: flex; align-items: center; gap: 12px;
  }
  .brand__dot { border-radius: 50%; flex: none; }
  .brand__name { font-weight: 500; line-height: 1; letter-spacing: -0.5px; }

  .card--front .brand { left: 67px; top: 150px; }
  .card--front .brand__dot { width: 52px; height: 52px; background: var(--brand-grey); }
  .card--front .brand__name { font-size: 44px; color: var(--brand-green); }

  .divider {
    position: absolute; left: 338px; top: 78px; width: 1px; height: 210px;
    background: linear-gradient(to bottom, transparent, var(--divider) 20%, var(--divider) 80%, transparent);
  }

  .contact {
    position: absolute; left: 367px; top: 78px; width: 215px;
    color: var(--text-dark); white-space: nowrap;
  }
  .contact__name { font-size: 20px; font-weight: 700; color: var(--brand-green); line-height: 22px; }
  .contact__role { font-size: 14px; font-weight: 500; color: var(--text-mid); line-height: 20px; }
  .contact__address { margin-top: 10px; font-size: 14px; line-height: 19px; }
  .contact__list { list-style: none; margin-top: 9px; font-size: 14px; line-height: 19px; }
  .contact__list li { display: flex; align-items: center; gap: 9px; }
  .contact__list svg { width: 13px; height: 13px; fill: var(--brand-green); flex: none; }

  .card--back .brand { left: 50%; top: 128px; transform: translateX(-50%); gap: 14px; }
  .card--back .brand__dot { width: 66px; height: 66px; background: var(--white); }
  .card--back .brand__name { font-size: 52px; color: var(--white); }

  .card__url {
    position: absolute; left: 0; right: 0; top: 292px; text-align: center;
    color: var(--white); font-size: 14px; letter-spacing: 6px;
  }
</style>
</head>
<body>
<main class="canvas">
  <section class="card card--front" aria-label="Business card front">
    <div class="brand">
      <span class="brand__dot"></span>
      <span class="brand__name">Plavex</span>
    </div>
    <div class="divider"></div>
    <div class="contact">
      <p class="contact__name">HARRIET DUNMORE</p>
      <p class="contact__role">CEO/FOUNDER</p>
      <p class="contact__address">Brackwell House<br>Fenmoor Enterprise Park<br>Partridge Way, QB9 3KX</p>
      <ul class="contact__list">
        <li><svg viewBox="0 0 16 16"><path d="M3.5 1l2.5 3-1.5 1.8c.8 1.9 2.2 3.3 4.2 4.2L10.5 8.5l3 2.5-1.5 3C6.5 14 2 9.5 2 3z"/></svg>01632 960418</li>
        <li><svg viewBox="0 0 16 16"><path d="M4.5 1h7v14h-7zM6 3v9h4V3zM7.3 13h1.4v1H7.3z"/></svg>07700 900562</li>
        <li><svg viewBox="0 0 16 16"><path d="M4 1h8v4H4zM1 6h14v6h-3v3H4v-3H1zM5 10v3h6v-3z"/></svg>01632 960733</li>
        <li><svg viewBox="0 0 16 16"><path d="M1 3h14v10H1zM2.5 4.5L8 9l5.5-4.5v-.5h-11z"/></svg>Harriet@plavex.co.uk</li>
        <li><svg viewBox="0 0 16 16"><path d="M8 1a7 7 0 1 0 0 14A7 7 0 0 0 8 1zm-1 2.5c-.5 1-1.8 1.5-2 2.5.5 1 2 .8 2.5 2-.5 1.2.2 2.5-.5 4A5.5 5.5 0 0 1 7 3.5zm3 .3c1.6.7 2.7 2.2 3 4-1 .2-1.5-.8-2.5-.5-.3-1-1.5-1.5-.5-3.5z"/></svg>www.plavex.co.uk</li>
      </ul>
    </div>
  </section>

  <section class="card card--back" aria-label="Business card back">
    <div class="brand">
      <span class="brand__dot"></span>
      <span class="brand__name">Plavex</span>
    </div>
    <p class="card__url">www.plavex.co.uk</p>
  </section>
</main>
</body>
</html>
```